KLW AUDITION

I need a post card design (front only) with this on it:
Bold Rising Steps (this is the main title to be in all caps)
Auditions
Date: Thursday June 30th
6:30-8:30 PM in person
Address: 4172 Fernwick BLVD, Oakland CA 94603
video submissions turn in by Sunday July 3rd, 2022 email:BoldRisingSteps22@tolvamail.com
Teens and Adults welcomed

SO PLEASE COME UP WITH A DESIGN THATS COLORFUL AND INVITING THX!

```html
<!DOCTYPE html>
<html lang="en">
<head>
<meta charset="utf-8">
<title>KLW Audition Postcard</title>
<link rel="stylesheet" href="https://fonts.googleapis.com/css2?family=Krona+One&family=Montserrat:wght@500;600;700&family=Oswald:wght@700&display=swap">
<style>
  :root {
    --page: #ffffff;
    --ink: #ffffff;
    --night: #05040a;
    --violet: #4a1f7a;
    --indigo: #2a1b6e;
    --magenta: #d6268f;
    --cyan: #16e0e0;
    --teal: #0e7c9a;
    --rule: rgba(255,255,255,0.35);
  }
  * { margin: 0; padding: 0; box-sizing: border-box; }
  html, body { width: 800px; height: 1200px; overflow: hidden; background: var(--page); }
  .postcard {
    position: absolute; left: 20px; top: 328px; width: 760px; height: 543px; overflow: hidden;
    color: var(--ink); font-family: "Montserrat", sans-serif;
    background:
      radial-gradient(ellipse 45% 22% at 80% 92%, rgba(214,38,143,0.75), transparent 70%),
      radial-gradient(ellipse 40% 35% at 78% 12%, rgba(150,70,200,0.7), transparent 70%),
      linear-gradient(100deg, var(--night) 0%, var(--night) 35%, var(--indigo) 65%, var(--violet) 100%);
  }
  .dancer-photo {
    position: absolute; left: 470px; top: 40px; width: 270px; height: 490px; border-radius: 130px 130px 40px 40px;
    background: radial-gradient(ellipse 60% 45% at 50% 45%, rgba(240,235,245,0.8), rgba(200,150,190,0.4) 60%, transparent 80%);
  }
  .title { position: absolute; left: 48px; top: 42px; font-family: "Krona One", sans-serif; font-weight: 400; line-height: 1; font-style: italic; }
  .title-line { display: block; font-size: 44px; letter-spacing: -1px; }
  .title-line + .title-line { margin-top: 6px; }
  .title-accent {
    display: block; margin-top: 10px; font-size: 72px; letter-spacing: -2px;
    background: linear-gradient(90deg, var(--teal), var(--cyan) 35%, #9a6cc0 65%, var(--magenta));
    -webkit-background-clip: text; background-clip: text; color: transparent;
  }
  .accent-bar { position: absolute; left: 67px; top: 230px; width: 63px; height: 7px; border-radius: 4px; background: var(--magenta); }
  .rule { position: absolute; left: 48px; width: 401px; height: 1px; background: var(--rule); }
  .rule-top { top: 233px; }
  .rule-bottom { top: 423px; }
  .event-label { position: absolute; left: 48px; top: 252px; font-size: 21px; font-weight: 700; letter-spacing: 1px; }
  .event-weekday { color: var(--magenta); margin-left: 10px; }
  .event-date { position: absolute; left: 46px; top: 285px; display: flex; align-items: flex-start; }
  .date-day { font-family: "Oswald", sans-serif; font-weight: 700; font-size: 56px; line-height: 1; color: var(--magenta); }
  .date-rest { margin-left: 6px; margin-top: 2px; line-height: 1; }
  .date-month { font-size: 19px; font-weight: 700; }
  .date-month sup { color: var(--magenta); font-size: 19px; vertical-align: baseline; margin-right: 8px; }
  .date-year { font-size: 32px; font-weight: 500; letter-spacing: 2px; display: block; margin-top: 2px; }
  .divider { position: absolute; width: 0; border-left: 1px dashed var(--rule); }
  .divider-date { left: 225px; top: 294px; height: 46px; }
  .event-time { position: absolute; left: 244px; top: 290px; line-height: 1.1; }
  .time-range { display: block; font-size: 23px; font-weight: 700; color: var(--cyan); letter-spacing: 1px; }
  .time-mode { display: block; font-size: 27px; font-weight: 500; letter-spacing: 1px; }
  .venue { position: absolute; left: 48px; top: 358px; display: flex; gap: 10px; font-size: 19px; font-weight: 700; font-style: normal; line-height: 1.3; }
  .venue svg { flex: none; margin-top: 3px; }
  .deadline { position: absolute; left: 46px; top: 436px; font-size: 12.5px; font-weight: 600; line-height: 1.35; }
  .deadline-box { display: inline-block; margin-top: 8px; padding: 2px 7px; border: 1.5px solid var(--magenta); font-size: 12.5px; font-weight: 700; letter-spacing: 0.5px; }
  .divider-info { left: 249px; top: 448px; height: 52px; }
  .contact { position: absolute; left: 268px; top: 440px; line-height: 1.25; }
  .contact-email { display: block; font-size: 12.5px; font-weight: 600; }
  .audience { display: block; margin-top: 6px; font-size: 15px; font-weight: 700; letter-spacing: 0.5px; }
  .audience-accent { display: block; font-size: 15px; font-weight: 700; color: var(--cyan); letter-spacing: 0.5px; }
</style>
</head>
<body>
  <main class="postcard">
    <div class="dancer-photo" role="img" aria-label="Photo of a ballerina in a white tutu standing en pointe under soft stage lights"></div>

    <h1 class="title">
      <span class="title-line">BOLD</span>
      <span class="title-line">RISING</span>
      <span class="title-accent">STEPS</span>
    </h1>
    <div class="rule rule-top"></div>
    <div class="accent-bar"></div>

    <h2 class="event-label">AUDITIONS<span class="event-weekday">THURSDAY</span></h2>
    <div class="event-date">
      <span class="date-day">30</span>
      <span class="date-rest">
        <span class="date-month"><sup>TH</sup>JUNE</span>
        <span class="date-year">2022</span>
      </span>
    </div>
    <div class="divider divider-date"></div>
    <div class="event-time">
      <span class="time-range">6:30-8:30 PM</span>
      <span class="time-mode">IN PERSON</span>
    </div>

    <address class="venue">
      <svg width="18" height="24" viewBox="0 0 18 24" aria-hidden="true">
        <path d="M9 0C4 0 0 4 0 9c0 6.5 9 15 9 15s9-8.5 9-15c0-5-4-9-9-9z" fill="#d6268f"/>
        <circle cx="9" cy="9" r="3.5" fill="#05040a"/>
      </svg>
      <span>4172 Fernwick BLVD, Oakland<br>CA 94603</span>
    </address>
    <div class="rule rule-bottom"></div>

    <div class="deadline">
      Video submissions<br>turn in by<br>
      <span class="deadline-box">SUNDAY JULY 3RD, 2022</span>
    </div>
    <div class="divider divider-info"></div>
    <div class="contact">
      <span class="contact-email">BoldRisingSteps22@tolvamail.com</span>
      <span class="audience">Teens and Adults</span>
      <span class="audience-accent">welcomed</span>
    </div>
  </main>
</body>
</html>
```